Velmora Systems Website

Website design for our company: Velmora Systems.
The website should look fresh and IT focused. Please have a look at http://www.velmorasystems.example.au/ for our current design. We want something fresh and new, professional looking, in WordPress so we can easily make changes.

It Company

```html
<!DOCTYPE html>
<html lang="en">
<head>
<meta charset="utf-8">
<title>Velmora Systems</title>
<link href="https://fonts.googleapis.com/css2?family=Roboto:wght@300;400;500;700&display=swap" rel="stylesheet">
<style>
  :root {
    --green: #1fb25a;
    --green-soft: #4cc27a;
    --green-bright: #3fbf2c;
    --ink: #333333;
    --slate: #3a3a48;
    --grey-text: #9a9a9a;
    --line: #cfcfcf;
    --footer-bg: #262626;
    --footer-text: #9b9b9b;
    --white: #ffffff;
  }
  * { box-sizing: border-box; margin: 0; padding: 0; }
  html, body { width: 769px; height: 1200px; overflow: hidden; background: var(--white); }
  body { position: relative; font-family: "Roboto", Arial, sans-serif; color: var(--ink); }
  .abs { position: absolute; }

  /* Header */
  .site-header { position: absolute; left: 0; top: 0; width: 769px; height: 77px; background: var(--white); }
  .brand { left: 64px; top: 11px; width: 150px; height: 58px; display: flex; align-items: center; gap: 8px; }
  .brand-mark { width: 14px; height: 14px; background: var(--green); border-radius: 50%; flex: none; }
  .brand-name { font-size: 14px; font-weight: 700; color: var(--green); white-space: nowrap; }
  .main-nav { left: 260px; top: 0; height: 77px; display: flex; }
  .main-nav a { display: block; height: 77px; line-height: 80px; font-size: 9.5px; color: var(--ink); text-decoration: none; padding: 0 7.5px; white-space: nowrap; }
  .main-nav a.active { background: var(--green); color: var(--white); width: 47px; padding: 0; text-align: center; margin-right: 2px; }

  /* Hero */
  .hero { left: 0; top: 77px; width: 769px; height: 267px; background: linear-gradient(120deg, #f2f2f2 0%, #bdbdbd 35%, #6b6b6b 60%, #9d9d9d 80%, #d8d8d8 100%); }
  .slider-dots { left: 355px; top: 326px; display: flex; gap: 9px; }
  .slider-dots span { width: 7px; height: 7px; border-radius: 50%; border: 1px solid #aaa; }
  .slider-dots span.on { background: var(--white); border-color: var(--white); }

  /* Features */
  .feature { width: 200px; top: 382px; text-align: center; }
  .feature-icon { display: block; margin: 0 auto; width: 60px; height: 60px; }
  .feature-title { margin-top: 38px; font-size: 19px; font-weight: 300; color: var(--green-soft); white-space: nowrap; }
  .feature-sub { font-size: 12px; font-weight: 400; color: #555; margin-top: 0; }
  .feature-text { position: absolute; width: 200px; top: 531px; font-size: 8.8px; line-height: 14.5px; color: var(--grey-text); }
  .more-btn { position: absolute; top: 595px; display: flex; height: 29px; }
  .more-btn .label { width: 71px; background: var(--green-soft); color: var(--white); font-size: 9.5px; line-height: 29px; text-align: center; }
  .more-btn .arrow { width: 29px; background: var(--slate); display: flex; align-items: center; justify-content: center; }

  .divider { left: 64px; width: 643px; height: 3px; border-top: 1px dashed var(--line); border-bottom: 1px dashed var(--line); }

  /* News */
  .section-title { left: 0; width: 769px; top: 668px; text-align: center; font-size: 19px; font-weight: 300; letter-spacing: .5px; color: var(--ink); }
  .news-card { top: 707px; width: 203px; text-align: center; }
  .news-photo { width: 203px; height: 109px; }
  .news-title { margin-top: 11px; font-size: 13.5px; font-weight: 500; color: var(--green); }
  .news-text { margin-top: 4px; font-size: 7.5px; line-height: 11px; color: var(--grey-text); padding: 0 6px; }
  .see-all { left: 313px; top: 900px; width: 143px; height: 32px; background: var(--green); color: var(--white); font-size: 12.5px; font-weight: 500; line-height: 32px; text-align: center; }

  /* Footer */
  .site-footer { left: 0; top: 987px; width: 769px; height: 180px; background: var(--footer-bg); }
  .footer-col { top: 1014px; }
  .footer-col h4 { font-size: 11.5px; font-weight: 400; color: var(--white); margin-bottom: 9px; }
  .footer-col li { list-style: none; font-size: 8px; line-height: 17.3px; color: var(--footer-text); white-space: nowrap; }
  .footer-col li.current { color: var(--green-soft); }
  .contact-row { display: flex; align-items: center; gap: 8px; font-size: 8px; color: var(--footer-text); height: 20px; margin-bottom: 2px; white-space: nowrap; }
  .contact-row .phone { color: var(--white); font-size: 11px; }
  .contact-row .mail { color: var(--green-soft); font-size: 9px; }
  .social { display: flex; gap: 10px; margin-top: 6px; }
  .social span { width: 9px; height: 9px; border-radius: 50%; background: #8a8a8a; }
  .remote-hint { font-size: 9px; color: var(--footer-text); margin-bottom: 10px; }
  .code-input { width: 162px; height: 23px; background: var(--white); font-size: 8px; color: #aaa; line-height: 23px; padding-left: 8px; }
  .connect-btn { margin-top: 9px; width: 162px; height: 24px; background: linear-gradient(var(--green-bright), #2aa41c); color: var(--white); font-size: 10px; line-height: 24px; text-align: center; }
  .copyright { left: 0; top: 1167px; width: 769px; height: 33px; background: var(--green); color: var(--white); font-size: 9px; line-height: 33px; text-align: center; }
</style>
</head>
<body>

<header class="site-header">
  <div class="abs brand"><span class="brand-mark"></span><span class="brand-name">Velmora Systems</span></div>
  <nav class="abs main-nav">
    <a class="active" href="#">HOME</a>
    <a href="#">SUPPLIERS</a>
    <a href="#">SERVICES</a>
    <a href="#">SUPPORTS</a>
    <a href="#">TESTIMONIALS</a>
    <a href="#">CONTACT US</a>
    <a href="#">ABOUT US</a>
  </nav>
</header>

<div class="abs hero" role="img" aria-label="Black and white photo of a hand on a computer mouse beside a laptop"></div>
<div class="abs slider-dots"><span class="on"></span><span></span><span></span></div>

<div class="abs feature" style="left:79px">
  <svg class="feature-icon" viewBox="0 0 64 64" aria-hidden="true">
    <path d="M12 30 A20 20 0 0 1 47 17" fill="none" stroke="var(--green-soft)" stroke-width="8"/>
    <path d="M40 8 L56 12 L50 27 Z" fill="var(--green-soft)"/>
    <path d="M52 34 A20 20 0 0 1 17 47" fill="none" stroke="var(--green-soft)" stroke-width="8"/>
    <path d="M24 56 L8 52 L14 37 Z" fill="var(--green-soft)"/>
  </svg>
  <div class="feature-title">COMPUTER REPAIR</div>
  <div class="feature-sub">DOLORE IPSUM</div>
</div>
<p class="feature-text" style="left:83px">Lorem ipsum dolor sit amet, consectetur adipisc elit. Proin ultricies vestibulum velit. bibendum condimentum metusip dolore ipsum.</p>
<div class="more-btn" style="left:83px"><span class="label">MORE INFO</span><span class="arrow"><svg width="8" height="10" viewBox="0 0 8 10"><path d="M1 1 L6 5 L1 9" fill="none" stroke="#fff" stroke-width="2"/></svg></span></div>

<div class="abs feature" style="left:283px">
  <svg class="feature-icon" viewBox="0 0 64 64" aria-hidden="true">
    <g fill="var(--green-soft)">
      <circle cx="24" cy="36" r="13"/>
      <g stroke="var(--green-soft)" stroke-width="7">
        <line x1="24" y1="17" x2="24" y2="55"/><line x1="5" y1="36" x2="43" y2="36"/>
        <line x1="11" y1="23" x2="37" y2="49"/><line x1="37" y1="23" x2="11" y2="49"/>
      </g>
      <circle cx="47" cy="16" r="7"/>
      <g stroke="var(--green-soft)" stroke-width="4">
        <line x1="47" y1="5" x2="47" y2="27"/><line x1="36" y1="16" x2="58" y2="16"/>
        <line x1="40" y1="9" x2="54" y2="23"/><line x1="54" y1="9" x2="40" y2="23"/>
      </g>
      <circle cx="49" cy="46" r="7"/>
      <g stroke="var(--green-soft)" stroke-width="4">
        <line x1="49" y1="35" x2="49" y2="57"/><line x1="38" y1="46" x2="60" y2="46"/>
        <line x1="42" y1="39" x2="56" y2="53"/><line x1="56" y1="39" x2="42" y2="53"/>
      </g>
    </g>
    <circle cx="24" cy="36" r="5" fill="#fff"/><circle cx="47" cy="16" r="3" fill="#fff"/><circle cx="49" cy="46" r="3" fill="#fff"/>
  </svg>
  <div class="feature-title">OUR SERVICES</div>
  <div class="feature-sub">DOLORE IPSUM</div>
</div>
<p class="feature-text" style="left:288px">Lorem ipsum dolor sit amet, consectetur adipisc elit. Proin ultricies vestibulum velit. bibendum condimentum metusip dolore ipsum.</p>
<div class="more-btn" style="left:288px"><span class="label">MORE INFO</span><span class="arrow"><svg width="8" height="10" viewBox="0 0 8 10"><path d="M1 1 L6 5 L1 9" fill="none" stroke="#fff" stroke-width="2"/></svg></span></div>

<div class="abs feature" style="left:488px">
  <svg class="feature-icon" viewBox="0 0 64 64" aria-hidden="true">
    <path d="M14 6 L24 6 L28 20 L21 26 C25 35 30 40 38 44 L44 37 L58 41 L58 51 C58 55 55 58 51 58 C28 56 8 36 6 13 C6 9 9 6 14 6 Z" fill="var(--green-soft)"/>
  </svg>
  <div class="feature-title">OUR SUPPORT</div>
  <div class="feature-sub">DOLORE IPSUM</div>
</div>
<p class="feature-text" style="left:493px">Lorem ipsum dolor sit amet, consectetur adipisc elit. Proin ultricies vestibulum velit. bibendum condimentum metusip dolore ipsum.</p>
<div class="more-btn" style="left:493px"><span class="label">MORE INFO</span><span class="arrow"><svg width="8" height="10" viewBox="0 0 8 10"><path d="M1 1 L6 5 L1 9" fill="none" stroke="#fff" stroke-width="2"/></svg></span></div>

<div class="abs divider" style="top:646px"></div>

<h2 class="abs section-title">LATEST NEWS</h2>

<article class="abs news-card" style="left:65px">
  <div class="news-photo" role="img" aria-label="Photo of a technician at a workbench with a computer tower" style="background:linear-gradient(135deg,#d9dde3,#8c8f95 55%,#4a4c50)"></div>
  <h3 class="news-title">Excepteur sint occaecat</h3>
  <p class="news-text">Lorem ipsum dolor sit amet, consectetur adipiscing elit. Sed blandit massa vel mauris sollicitudin dignissim...</p>
</article>
<article class="abs news-card" style="left:284px">
  <div class="news-photo" role="img" aria-label="Photo of two colleagues working at a desktop computer" style="background:linear-gradient(135deg,#eceae6,#b4b0a8 55%,#5b5a58)"></div>
  <h3 class="news-title">Sunt in culpa qui officia</h3>
  <p class="news-text">Lorem ipsum dolor sit amet, consectetur adipiscing elit. Sed blandit massa vel mauris sollicitudin dignissim...</p>
</article>
<article class="abs news-card" style="left:501px">
  <div class="news-photo" role="img" aria-label="Photo of a repair desk crowded with monitors and equipment" style="background:linear-gradient(135deg,#c9ccd0,#7b7f86 50%,#3e4044)"></div>
  <h3 class="news-title">Cupidatat non proident</h3>
  <p class="news-text">Lorem ipsum dolor sit amet, consectetur adipiscing elit. Sed blandit massa vel mauris sollicitudin dignissim...</p>
</article>

<div class="abs see-all">See all news</div>

<div class="abs divider" style="top:956px"></div>

<footer class="abs site-footer"></footer>

<div class="abs footer-col" style="left:64px">
  <h4>Navigation</h4>
  <ul><li class="current">Home</li><li>About</li><li>Services</li><li>News</li><li>Contacts</li></ul>
</div>
<div class="abs footer-col" style="left:163px">
  <h4>Categories</h4>
  <ul><li>Same Day In-Home Support</li><li>Certified Technicians</li><li>Virus &amp; Spyware Removal</li><li>Wireless Networking</li><li>On-site Engineers</li><li>Directory, Mail &amp; Database</li></ul>
</div>
<div class="abs footer-col" style="left:311px">
  <h4>Contacts</h4>
  <div class="contact-row">
    <svg width="12" height="11" viewBox="0 0 12 11"><path d="M6 0 L12 5 L10 5 L10 11 L7 11 L7 7 L5 7 L5 11 L2 11 L2 5 L0 5 Z" fill="var(--green-soft)"/></svg>
    <span>27 Harbour Lane Kestrel Bay 5090 Australia</span>
  </div>
  <div class="contact-row">
    <svg width="12" height="12" viewBox="0 0 64 64"><path d="M14 6 L24 6 L28 20 L21 26 C25 35 30 40 38 44 L44 37 L58 41 L58 51 C58 55 55 58 51 58 C28 56 8 36 6 13 C6 9 9 6 14 6 Z" fill="var(--green-soft)"/></svg>
    <span>Call us: <span class="phone">+ 0855501742</span></span>
  </div>
  <div class="contact-row">
    <svg width="12" height="10" viewBox="0 0 12 10"><rect x="0.5" y="0.5" width="11" height="9" fill="none" stroke="var(--green-soft)"/><path d="M0.5 0.5 L6 5.5 L11.5 0.5" fill="none" stroke="var(--green-soft)"/></svg>
    <span class="mail">hello@velmorasystems.example.au</span>
  </div>
  <div class="social"><span></span><span></span><span></span></div>
</div>
<div class="abs footer-col" style="left:543px">
  <h4>Remote Support</h4>
  <p class="remote-hint">Enter your 6-digit code</p>
  <div class="code-input">Enter your 6-digit code</div>
  <div class="connect-btn">Connect Now</div>
</div>

<div class="abs copyright">© 2014 Velmora Systems All Rights Reserved. Designed &amp; Developed by Northpine Studio</div>

</body>
</html>
```